Website re-design and completion for www.brovimark.com

Graphically redesign and complete the existing site www.brovimark.com
This site intent is to:
a) introduce and educate about a new Technoloy to customers in a variety of different industries using traditional methods.
b) outline and promote the benefits and ROI of using the new techology
c) Sell our machines by showing customers the benefits and reasons to purchase from us over other suppliers
We do want to keep the overall concept. Like the home page with a slider. The most important thing to us is to increase the design of the slider. Next we need it standard layout with some attractive design to describe each product group. There are 3 product groups. Laser Cleaning Machines, Laser Welding Machines and Laser Cutting Machines

Target Market(s)

Mostly business to business.

Coding

Coded - Design and coding required

Font styles to use
Sans Serif
Other font styles liked:
• Calibri, Arial

Requirements
Must have
• A serious approach as we are targeting professionals, such as production managers, engineers and so forth
Should not have
• Annoying call to action stuff. Overly playful gimmicks.

```html
<!DOCTYPE html>
<html lang="en">
<head>
<meta charset="utf-8">
<title>Brovimark – Laser Machines</title>
<link href="https://fonts.googleapis.com/css2?family=Montserrat:wght@500;600;700&family=Lato:wght@400;700&display=swap" rel="stylesheet">
<style>
  :root {
    --blue: #0a7dc7;
    --red: #c1272d;
    --ink: #222222;
    --text: #333333;
    --grey-band: #f2f2f2;
    --white: #ffffff;
  }
  * { box-sizing: border-box; margin: 0; padding: 0; }
  html, body { width: 1200px; height: 3336px; overflow: hidden; }
  body { position: relative; background: var(--white); font-family: "Lato", Arial, sans-serif; color: var(--text); }
  .abs { position: absolute; }
  .heading { font-family: "Montserrat", Arial, sans-serif; font-weight: 700; font-size: 38px; color: var(--ink); letter-spacing: 0.5px; }
  .heading .accent { color: var(--blue); }
  .rule { position: absolute; height: 4px; width: 70px; background: var(--red); }
  .btn { position: absolute; display: flex; align-items: center; justify-content: center; background: var(--red); color: var(--white); font-family: "Lato", Arial, sans-serif; font-weight: 700; font-size: 15px; border-radius: 3px; text-transform: uppercase; letter-spacing: 0.3px; }

  /* header */
  .site-header { position: absolute; left: 0; top: 0; width: 1200px; height: 93px; background: var(--white); }
  .brand { position: absolute; display: flex; align-items: center; gap: 10px; font-family: "Montserrat", Arial, sans-serif; font-weight: 700; color: var(--red); letter-spacing: 2px; }
  .brand .mark { background: var(--blue); border-radius: 50%; }
  .main-nav { position: absolute; top: 38px; left: 678px; display: flex; gap: 53px; font-size: 16px; color: var(--ink); }

  /* hero */
  .hero { position: absolute; left: 0; top: 93px; width: 1200px; height: 600px;
    background: linear-gradient(100deg, #1b1a1a 0%, #2c2621 35%, #7a4a1f 60%, #d98a2c 75%, #5a3c22 100%); }
  .hero-kicker { left: 124px; top: 195px; font-family: "Montserrat", Arial, sans-serif; font-weight: 600; font-size: 31px; color: var(--white); }
  .hero-title { left: 122px; top: 232px; font-family: "Montserrat", Arial, sans-serif; font-weight: 700; font-size: 70px; color: var(--white); }
  .hero-copy { left: 124px; top: 328px; width: 360px; font-size: 15.5px; line-height: 21.5px; color: var(--white); }

  /* about */
  .about-photo-back { left: 121px; top: 799px; width: 368px; height: 402px; background: linear-gradient(135deg, #8f8a86 0%, #c9473b 45%, #e07a2b 80%, #f0b247 100%); }
  .about-photo-front { left: 254px; top: 981px; width: 347px; height: 334px; background: radial-gradient(circle at 55% 70%, #f2b043 0%, #6b5a45 25%, #2f3a45 60%, #1d242b 100%); border: 2px solid var(--white); }
  .about-title { left: 681px; top: 855px; }
  .about-copy { left: 681px; top: 948px; width: 395px; font-size: 15px; line-height: 25.7px; color: var(--text); }

  /* benefits */
  .benefits { position: absolute; left: 0; top: 1425px; width: 1200px; height: 426px; background: var(--grey-band); }
  .benefit { position: absolute; top: 191px; width: 200px; text-align: center; }
  .benefit .badge { width: 102px; height: 102px; margin: 0 auto; border-radius: 50%; border: 2px solid var(--blue); background: var(--white); display: flex; align-items: center; justify-content: center; }
  .benefit .badge.active { background: var(--blue); }
  .benefit .label { margin-top: 18px; font-family: "Montserrat", Arial, sans-serif; font-weight: 600; font-size: 17.5px; color: var(--ink); }

  /* products */
  .product { position: absolute; top: 2049px; width: 298px; height: 291px; overflow: hidden; }
  .product .photo { position: absolute; inset: 0; }
  .product .tag { position: absolute; left: 0; bottom: 0; width: 298px; height: 50px; }
  .product .tag span { position: absolute; left: 70px; top: 14px; font-family: "Montserrat", Arial, sans-serif; font-weight: 600; font-size: 16.5px; color: var(--ink); }
  .product.featured .tag span { color: var(--white); }

  /* why */
  .why { position: absolute; left: 0; top: 2442px; width: 1200px; height: 503px;
    background: linear-gradient(90deg, var(--blue) 0%, var(--blue) 52%, #2a6eb6 64%, #3b5f9a 80%, #2b3f66 100%); }
  .why-title { left: 111px; top: 70px; color: var(--white); }
  .why-copy { left: 111px; top: 160px; width: 445px; font-size: 15px; line-height: 25.7px; color: var(--white); }

  /* footer */
  .footer-nav { position: absolute; top: 3143px; left: 0; width: 1200px; display: flex; justify-content: center; gap: 44px; font-size: 17px; color: var(--ink); }
  .copyright { position: absolute; top: 3195px; left: 0; width: 1200px; text-align: center; font-size: 16px; color: var(--text); }
  .social { position: absolute; top: 3244px; left: 501px; display: flex; gap: 8px; }
  .social span { width: 44px; height: 44px; border-radius: 50%; background: var(--white); box-shadow: 0 1px 6px rgba(0,0,0,0.15); }
  .social span.primary { background: var(--blue); }
</style>
</head>
<body>

<header class="site-header">
  <div class="brand" style="left:111px; top:28px; font-size:34px;">
    <span class="mark" style="width:16px; height:16px;"></span>BROVIMARK
  </div>
  <nav class="main-nav"><span>Home</span><span>Products</span><span>Services</span><span>Contact Us</span></nav>
</header>

<section class="hero" role="img" aria-label="Close-up photo of a laser head cutting metal with bright orange sparks">
  <p class="abs hero-kicker">Welcome To</p>
  <h1 class="abs hero-title">Brovimark</h1>
  <p class="abs hero-copy">Lorem ipsum dolor sit amet, consectetur adipiscing elit, sed do eiusmod tempor incididunt ut labore et dolore magna aliqua.</p>
  <a class="btn" style="left:124px; top:423px; width:133px; height:52px;">Get Started</a>
</section>

<section class="about">
  <svg class="abs" style="left:150px; top:840px;" width="400" height="420" viewBox="0 0 400 420">
    <polyline points="339,6 380,6 380,140" fill="none" stroke="var(--blue)" stroke-width="4"/>
    <polyline points="11,360 11,411 104,411" fill="none" stroke="var(--blue)" stroke-width="4"/>
  </svg>
  <div class="abs about-photo-back" role="img" aria-label="Photo of a handheld laser welding torch in a gloved hand"></div>
  <div class="abs about-photo-front" role="img" aria-label="Photo of a laser cutting head throwing sparks over a metal sheet"></div>
  <h2 class="abs heading about-title">ABOUT <span class="accent">US</span></h2>
  <div class="rule" style="left:681px; top:911px;"></div>
  <p class="abs about-copy">Lorem ipsum dolor sit amet, consectetur adipiscing elit, sed do eiusmod tempor incididunt ut labore et dolore magna aliqua. Ut enim ad minim veniam, quis nostrud exercitation ullamco laboris nisi ut aliquip ex ea commodo consequat. Duis aute irure dolor in reprehenderit in voluptate velit esse cillum dolore eu fugiat nulla pariatur. Excepteur sint occaecat cupidatat non proident, sunt in culpa qui officia deserunt mollit anim id est laborum.</p>
  <a class="btn" style="left:681px; top:1193px; width:129px; height:51px;">Learn More</a>
</section>

<section class="benefits">
  <h2 class="abs heading" style="left:0; width:1200px; text-align:center; top:72px;">OUR <span class="accent">BENEFITS</span></h2>
  <div class="rule" style="left:565px; top:130px;"></div>
  <div class="benefit" style="left:168px;">
    <div class="badge active"><svg width="44" height="44" viewBox="0 0 44 44" fill="none" stroke="#fff" stroke-width="2"><rect x="10" y="6" width="24" height="6"/><path d="M22 12v14M16 32h12M22 26l-4 6M22 26l4 6"/><path d="M6 38h32"/></svg></div>
    <p class="label">Sed ut perspiciatis</p>
  </div>
  <div class="benefit" style="left:390px;">
    <div class="badge"><svg width="44" height="44" viewBox="0 0 44 44" fill="none" stroke="var(--blue)" stroke-width="2"><rect x="14" y="6" width="16" height="8"/><path d="M22 14v12M10 36l12-10 12 10-12 4z"/></svg></div>
    <p class="label">Sed ut perspiciatis</p>
  </div>
  <div class="benefit" style="left:611px;">
    <div class="badge"><svg width="44" height="44" viewBox="0 0 44 44" fill="none" stroke="var(--blue)" stroke-width="2"><path d="M8 8h28M22 8v16"/><rect x="18" y="12" width="8" height="8"/><path d="M8 32h28l-4 6H12z"/></svg></div>
    <p class="label">Sed ut perspiciatis</p>
  </div>
  <div class="benefit" style="left:833px;">
    <div class="badge"><svg width="44" height="44" viewBox="0 0 44 44" fill="none" stroke="var(--blue)" stroke-width="2"><rect x="8" y="18" width="28" height="18"/><rect x="12" y="22" width="8" height="8"/><path d="M26 18V8h6v10M30 8l4-4"/></svg></div>
    <p class="label">Sed ut perspiciatis</p>
  </div>
</section>

<section class="products">
  <h2 class="abs heading" style="left:0; width:1200px; text-align:center; top:1943px;">OUR <span class="accent">PRODUCT</span></h2>
  <div class="rule" style="left:565px; top:2001px;"></div>

  <article class="product" style="left:111px;">
    <div class="photo" role="img" aria-label="Photo of a laser beam cleaning a rusted metal surface" style="background:linear-gradient(135deg,#6b5a48 0%,#3a322c 40%,#1f1c1a 70%,#111 100%);"></div>
    <svg class="tag" viewBox="0 0 298 50" preserveAspectRatio="none"><polygon points="36,0 298,0 298,50 0,50" fill="#fff"/></svg>
    <div class="tag"><span>Laser Cleaning Machines</span></div>
  </article>

  <article class="product featured" style="left:451px;">
    <div class="photo" role="img" aria-label="Photo of a laser welding machine in a factory hall with sparks" style="background:linear-gradient(160deg,#5f6d7a 0%,#3a3f44 40%,#b8741f 70%,#3a3633 100%);"></div>
    <svg class="tag" viewBox="0 0 298 50" preserveAspectRatio="none"><polygon points="36,0 298,0 298,50 0,50" fill="var(--blue)"/></svg>
    <div class="tag"><span>Laser Welding Machines</span></div>
  </article>

  <article class="product" style="left:791px;">
    <div class="photo" role="img" aria-label="Photo of a laser cutting nozzle above a metal sheet" style="background:linear-gradient(180deg,#8e97a3 0%,#a7b0bb 45%,#c9cdd3 70%,#9aa3ad 100%);"></div>
    <svg class="tag" viewBox="0 0 298 50" preserveAspectRatio="none"><polygon points="36,0 298,0 298,50 0,50" fill="#fff"/></svg>
    <div class="tag"><span>Laser Cutting Machines</span></div>
  </article>
</section>

<section class="why" role="img" aria-label="Photo of a laser cutting head engraving glowing lines in a metal plate">
  <h2 class="abs heading why-title">WHY BROVIMARK?</h2>
  <div class="rule" style="left:111px; top:123px;"></div>
  <p class="abs why-copy">At Brovimark, we're dedicated to providing you with top-of-the-line equipment that you can rely on for all your manufacturing requirements. With years of expertise in the manufacturing industry, we understand the importance of laser photonics equipment and the myriad questions that may arise when integrating laser technology into your operations. That's why we're here to offer comprehensive support and guidance every step of the way.</p>
  <a class="btn" style="left:112px; top:390px; width:129px; height:52px;">Learn More</a>
</section>

<footer>
  <div class="brand" style="left:0; width:1200px; justify-content:center; top:3063px; font-size:44px;">
    <span class="mark" style="width:20px; height:20px;"></span>BROVIMARK
  </div>
  <nav class="footer-nav"><span>Home</span><span>Products</span><span>Services</span><span>Contact Us</span></nav>
  <p class="copyright">©Copyrights 2024 Brovimark &nbsp;|&nbsp;&nbsp; All Rights Reserved</p>
  <div class="social" aria-label="Social media links">
    <span class="primary" aria-label="Social link"></span><span aria-label="Social link"></span><span aria-label="Social link"></span><span aria-label="Social link"></span>
  </div>
</footer>

</body>
</html>
```